Hvac and insulation company needs good looking business card design

We are hvac and insulation company and looking for a new business cards that look to today standards designs

Target Market(s)

homeowners

Industry/Entity Type

Hvac

Contact Information for Business Card

Name: Walter Brinoku
Home comfort consultant
address: 4827 Dunmore St #215 Oakland, CA 94619
office: 888-316-2790
cell: 510-742-3185
Lic.# 584261
Email: walter@corvane-hvac.com
Web: corvane-hvac.com

Requirements
Must have
• clean and sleek look
Nice to have
• simple with a clean look
Should not have
• to busy business card

```html
<!DOCTYPE html>
<html lang="en">
<head>
<meta charset="UTF-8">
<title>Corvane Home Solutions – Business Card</title>
<link rel="stylesheet" href="https://fonts.googleapis.com/css2?family=Open+Sans:wght@400;600;700&family=Oswald:wght@500&display=swap">
<style>
  :root {
    --bg: #3a3a3b;
    --card: #1f1f20;
    --orange: #f08c12;
    --white: #f2f2f2;
    --grey: #8a8a8a;
    --soft-grey: #b9b9b9;
  }
  * { box-sizing: border-box; margin: 0; padding: 0; }
  html, body { width: 1200px; height: 900px; overflow: hidden; }
  body {
    background: var(--bg);
    font-family: "Open Sans", Arial, sans-serif;
    position: relative;
  }
  .card {
    position: absolute;
    left: 250px;
    width: 700px;
    height: 400px;
    background: var(--card);
    overflow: hidden;
    box-shadow: 0 12px 30px rgba(0,0,0,.45);
  }
  .card-back { top: 35px; }
  .card-front { top: 465px; }

  /* Back */
  .back-brand {
    position: absolute;
    top: 140px; left: 0; right: 0;
    display: flex; align-items: center; justify-content: center; gap: 16px;
  }
  .brand-dot {
    width: 26px; height: 26px; border-radius: 50%;
  }
  .back-brand .brand-dot { background: var(--grey); }
  .back-brand .brand-name {
    font-size: 44px; font-weight: 600; color: var(--grey); letter-spacing: 1px;
  }
  .back-web {
    position: absolute;
    bottom: 46px; left: 0; right: 0;
    display: flex; align-items: center; justify-content: center; gap: 10px;
    font-size: 17px; color: var(--soft-grey); letter-spacing: .5px;
  }
  .accent { color: var(--orange); }

  /* Front */
  .front-brand {
    position: absolute;
    left: 40px; top: 140px;
    width: 310px;
    display: flex; align-items: center; gap: 14px;
  }
  .front-brand .brand-dot { background: var(--orange); flex: none; }
  .front-brand .brand-name {
    font-size: 30px; font-weight: 600; color: var(--orange); line-height: 1.15;
  }
  .divider {
    position: absolute;
    left: 372px; top: 45px;
    width: 2px; height: 235px;
    background: var(--white);
  }
  .contact {
    position: absolute;
    left: 398px; top: 45px;
    color: var(--white);
  }
  .person-name {
    font-family: "Oswald", "Arial Narrow", sans-serif;
    font-weight: 500; font-size: 36px; letter-spacing: 1px;
    text-transform: uppercase; line-height: 1;
  }
  .person-role {
    color: var(--orange); font-weight: 600; font-size: 16px;
    margin-top: 6px; letter-spacing: .5px;
  }
  .license { font-size: 17px; margin-top: 14px; }
  .contact-list { list-style: none; margin-top: 8px; }
  .contact-list li {
    display: flex; align-items: center; gap: 14px;
    font-size: 17px; height: 28px; letter-spacing: .3px;
  }
  .icon { width: 18px; height: 18px; flex: none; }
  .address {
    position: absolute;
    left: 120px; bottom: 30px;
    font-size: 19px; color: var(--white); letter-spacing: 1px;
  }
  .address .label { color: var(--orange); }
  .stripe {
    position: absolute;
    left: 0; right: 0; bottom: 0;
    height: 12px; background: var(--orange);
  }
</style>
</head>
<body>

<section class="card card-back" aria-label="Card back">
  <div class="back-brand">
    <span class="brand-dot"></span>
    <span class="brand-name">Corvane Home Solutions</span>
  </div>
  <div class="back-web">
    <svg class="icon" viewBox="0 0 20 20" fill="none" stroke="#f08c12" stroke-width="1.5">
      <circle cx="10" cy="10" r="8"/><ellipse cx="10" cy="10" rx="3.5" ry="8"/>
      <line x1="2" y1="10" x2="18" y2="10"/><line x1="3.5" y1="6" x2="16.5" y2="6"/><line x1="3.5" y1="14" x2="16.5" y2="14"/>
    </svg>
    <span>www.<span class="accent">corvane-hvac</span>.com</span>
  </div>
</section>

<section class="card card-front" aria-label="Card front">
  <div class="front-brand">
    <span class="brand-dot"></span>
    <span class="brand-name">Corvane Home Solutions</span>
  </div>

  <div class="divider"></div>

  <div class="contact">
    <h1 class="person-name">Walter Brinoku</h1>
    <p class="person-role">Home comfort consultant</p>
    <p class="license">Lic #584261</p>
    <ul class="contact-list">
      <li>
        <svg class="icon" viewBox="0 0 20 20" fill="none" stroke="#f08c12" stroke-width="1.6">
          <rect x="5" y="2" width="10" height="16" rx="1.5"/><line x1="8.5" y1="15" x2="11.5" y2="15"/>
        </svg>
        <span>888-316-2790</span>
      </li>
      <li>
        <svg class="icon" viewBox="0 0 20 20" fill="#f08c12">
          <path d="M5 2l3 3-1.6 2.2a10 10 0 0 0 6.4 6.4L15 12l3 3-2 3C9 18 2 11 2 4z"/>
        </svg>
        <span>510-742-3185</span>
      </li>
      <li>
        <svg class="icon" viewBox="0 0 20 20" fill="none" stroke="#f08c12" stroke-width="1.6">
          <rect x="2" y="4" width="16" height="12" rx="1"/><polyline points="2,5 10,11 18,5"/>
        </svg>
        <span>walter@corvane-hvac.com</span>
      </li>
      <li>
        <svg class="icon" viewBox="0 0 20 20" fill="none" stroke="#f08c12" stroke-width="1.5">
          <circle cx="10" cy="10" r="8"/><ellipse cx="10" cy="10" rx="3.5" ry="8"/>
          <line x1="2" y1="10" x2="18" y2="10"/><line x1="3.5" y1="6" x2="16.5" y2="6"/><line x1="3.5" y1="14" x2="16.5" y2="14"/>
        </svg>
        <span>www.<span class="accent">corvane-hvac</span>.com</span>
      </li>
    </ul>
  </div>

  <p class="address"><span class="label">Address</span> - 4827 Dunmore St #215 Oakland, CA 94619</p>
  <div class="stripe"></div>
</section>

</body>
</html>
```